The most modern business card ever !!!

Our company call “Vendalo”. Vendalo is a technology company specialized in cruises solutions. Out main product is a platform to reserve cruises. This is a revolutionary platform that make easier to travel agencies and final users to reserve cruises across dozen companies like tibba, wernu, hpv, dgb, etc..We are a “start up”, with a young team of developers and we want to transmit it.. For it, we want something different, a modern business card that represent cruises and technology.. When someone receive this card, this person should say: wowww this is different… this is modern… this is a cruise related company..
- diferent, modern
- traditions business card

```html
<!DOCTYPE html>
<html lang="en">
<head>
<meta charset="utf-8">
<title>Vendalo Business Card</title>
<link href="https://fonts.googleapis.com/css2?family=Exo+2:wght@500&family=Roboto:wght@400;500;700&display=swap" rel="stylesheet">
<style>
  :root {
    --backdrop: #e9eaec;
    --card-white: #ffffff;
    --ink: #111111;
    --sky-top: #4f87a6;
    --sky-mid: #7fa9bf;
    --sea-mid: #2f6f92;
    --sea-deep: #1f5a7c;
    --brand-blue: #2aa6dc;
    --teal-dark: #0f8fae;
    --teal-light: #2cb0e0;
  }
  * { margin: 0; padding: 0; box-sizing: border-box; }
  html, body {
    width: 1200px; height: 1200px; overflow: hidden;
    background: var(--backdrop);
  }
  .canvas {
    position: relative; width: 1200px; height: 1200px;
  }
  .card {
    position: absolute; top: 225px; width: 450px; height: 750px;
    overflow: hidden;
    box-shadow: 0 10px 30px rgba(0,0,0,0.18);
  }

  /* Front */
  .card-front { left: 130px; }
  .cruise-photo {
    position: absolute; inset: 0;
    background: linear-gradient(180deg,
      var(--sky-top) 0%, var(--sky-mid) 45%, #c9dbe4 58%,
      #e3ecf0 66%, var(--sea-mid) 72%, var(--sea-deep) 100%);
  }
  .accent-bar-front {
    position: absolute; left: 182px; top: 0; width: 86px; height: 290px;
    background: var(--card-white);
  }
  .brand-front {
    position: absolute; left: 78px; top: 310px;
    font-family: "Exo 2", "Roboto", sans-serif; font-weight: 500;
    font-size: 64px; letter-spacing: 1px; color: var(--card-white);
    line-height: 1;
  }
  .website-pill {
    position: absolute; left: 79px; top: 594px; width: 293px; height: 30px;
    background: var(--ink); border-radius: 10px;
    display: flex; align-items: center; justify-content: center;
    font-family: "Roboto", sans-serif; font-weight: 700; font-size: 17px;
    letter-spacing: 1.5px; color: var(--card-white);
  }
  .website-pill .site-name { color: var(--brand-blue); }

  /* Back */
  .card-back { left: 620px; background: var(--card-white); }
  .vertical {
    position: absolute; writing-mode: vertical-rl; transform: rotate(180deg);
  }
  .holder-name {
    left: 68px; top: 106px; height: 222px;
    font-family: "Roboto", sans-serif; font-weight: 700; font-size: 19px;
    letter-spacing: 3px; color: var(--ink);
  }
  .holder-title {
    left: 96px; top: 140px; height: 188px;
    font-family: "Roboto", sans-serif; font-weight: 400; font-size: 16px;
    letter-spacing: 2.5px; color: var(--ink);
  }
  .stripe-mark { position: absolute; left: 68px; top: 371px; }
  .brand-back {
    left: 248px; top: 106px; height: 294px;
    font-family: "Exo 2", "Roboto", sans-serif; font-weight: 500;
    font-size: 62px; line-height: 1; color: var(--ink);
  }
  .accent-bar-back {
    position: absolute; left: 324px; top: 106px; width: 56px; height: 294px;
    background: linear-gradient(90deg, var(--teal-dark), var(--teal-light) 50%, var(--teal-dark));
  }
  .divider {
    position: absolute; left: 68px; top: 528px; width: 192px; height: 4px;
    background: var(--ink);
  }
  .contact-list {
    position: absolute; left: 68px; top: 570px; list-style: none;
    font-family: "Roboto", sans-serif; font-size: 18px; letter-spacing: 1.5px;
    color: var(--ink);
  }
  .contact-list li { height: 39.5px; }
</style>
</head>
<body>
<main class="canvas">
  <section class="card card-front">
    <div class="cruise-photo" role="img" aria-label="Photo of a white cruise ship sailing on blue water under a cloudy sky, tinted blue"></div>
    <div class="accent-bar-front"></div>
    <div class="brand-front">Vendalo</div>
    <div class="website-pill">www.<span class="site-name">YourSite</span>.com</div>
  </section>

  <section class="card card-back">
    <div class="vertical holder-name">Your Name Here</div>
    <div class="vertical holder-title">Designation</div>
    <svg class="stripe-mark" width="56" height="29" viewBox="0 0 56 29" aria-hidden="true">
      <rect x="0" y="0" width="56" height="10" fill="var(--brand-blue)"/>
      <rect x="0" y="17" width="56" height="12" fill="var(--ink)"/>
    </svg>
    <div class="vertical brand-back">Vendalo</div>
    <div class="accent-bar-back"></div>
    <div class="divider"></div>
    <ul class="contact-list">
      <li>- Contact@me.com</li>
      <li>- 123 +4567 8910 111</li>
      <li>- Main Avenue Street 123. Etc</li>
    </ul>
  </section>
</main>
</body>
</html>
```